Kestrel Baseball & Softball Camp 2017

Design a flyer that will promote our 2017 summer camp for boys and girls softball.

Weeks of
July 10th - 14th
July 17th - 21st.

Players ages 5 - 11.
Full day = 9:30am - 2:30pm half day = 9:30am - 11:30am.
$295 / full day : $195/ half day

Hosted by "Kestrel Baseball" affiliated with the Harbor Comets Travel Baseball & Softball Club and the Maple Ridge Youth League,

Camp Location MRYL, Route 9C Birch Hollow.

PHone 555-240-7813, email info@kestrelball.example

The color should be "Red white and blue color scheme" with dates and location standing out. Kestrel Logo should be prominent MRYL and Comets smaller and secondary.

Feel free to use stock photo's if available. visit www.harborcomets.example for more pictures and there are links for the 2017 summer camp there with possibly some more information.

Target Market(s)

to catch the eye of parents of players ages 5 - 11 already at little league or shopping in local stores

Colors
ec1f27
0355a3
ffffff

Requirements
Must have
• red white and blue design,
• Kestrel logo and summer camp prominent so it catches the eye and explains what it is right away.
• the comets and maple ridge logo's a the bottom showing the affiliation.
Nice to have
• stock photo's or something showing players having a great time or a beautiful ballpark
Should not have
• to much clutter or hard to figure out what it's for

```html
<!DOCTYPE html>
<html lang="en">
<head>
<meta charset="utf-8">
<title>Kestrel Softball Summer Camp 2017</title>
<link href="https://fonts.googleapis.com/css2?family=Oswald:wght@400;500;600;700&family=Kaushan+Script&display=swap" rel="stylesheet">
<style>
  :root {
    --red: #ec1f27;
    --red-deep: #c8141c;
    --blue: #0355a3;
    --navy: #1d2f6b;
    --white: #ffffff;
    --ink: #1a1a1a;
    --rule: rgba(255,255,255,.8);
  }
  * { margin: 0; padding: 0; box-sizing: border-box; }
  html, body { width: 819px; height: 1200px; overflow: hidden; background: var(--white); }
  .flyer {
    position: relative; width: 819px; height: 1200px; overflow: hidden;
    font-family: "Oswald", sans-serif; color: var(--ink);
  }
  .backdrop { position: absolute; inset: 0; }
  .abs { position: absolute; }
  .script { font-family: "Kaushan Script", cursive; font-weight: 400; }

  .logo-badge {
    left: 43px; top: 245px; width: 260px; height: 260px; border-radius: 50%;
    background: var(--white); display: flex; align-items: center; justify-content: center;
  }
  .logo-badge span { font-weight: 700; font-size: 50px; color: var(--red); letter-spacing: 1px; }

  .sport-label { left: 496px; top: 458px; font-size: 54px; line-height: 1.2; color: var(--red); }
  .headline { left: 67px; top: 540px; }
  .year { left: 696px; top: 536px; }
  .audience { left: 538px; top: 638px; font-size: 27px; line-height: 1.2; color: var(--blue); }
  .hosted {
    left: 73px; top: 678px; font-weight: 600; font-size: 9.6px; line-height: 1.9;
    text-transform: uppercase; color: var(--ink); white-space: nowrap;
  }
  .partner-mark {
    left: 246px; top: 738px; width: 62px; height: 62px; border-radius: 50%;
    background: #7fb24a; border: 3px solid #e8c227;
  }

  .ages { left: 514px; top: 838px; display: flex; align-items: center; gap: 10px; }
  .ages-label { font-weight: 700; font-size: 30px; line-height: 1.08; color: var(--red-deep); text-transform: uppercase; }
  .ages-circle {
    left: 654px; top: 817px; width: 116px; height: 116px; border-radius: 50%;
    background: var(--navy); color: var(--white); font-weight: 700; font-size: 32px;
    display: flex; align-items: center; justify-content: center;
  }

  .info { color: var(--white); }
  .schedule { left: 42px; top: 935px; }
  .schedule h3 { font-weight: 700; font-size: 24px; line-height: 1.1; }
  .schedule p { font-size: 22px; font-weight: 600; line-height: 1.15; }
  .schedule .row { padding-left: 48px; }
  .dash { border-top: 2px dashed var(--rule); margin: 8px 0 8px 48px; width: 170px; }
  .icon { position: absolute; }

  .divider { top: 930px; width: 0; height: 130px; border-left: 2px dashed var(--rule); }
  .weeks { left: 300px; top: 925px; }
  .weeks .script { font-size: 26px; }
  .weeks p { font-weight: 700; font-size: 30px; line-height: 1.2; }
  .weeks .arrow { font-size: 16px; vertical-align: middle; margin-right: 6px; }
  .weeks .sep { border-top: 2px dashed var(--rule); width: 230px; margin: 4px 0; }

  .price { left: 580px; top: 925px; }
  .price .script { font-size: 26px; }
  .price .lines { padding-left: 52px; margin-top: 8px; font-weight: 600; font-size: 22px; line-height: 1.25; }

  .footer-rule { left: 30px; top: 1080px; width: 760px; border-top: 2px dashed var(--rule); }
  .register { left: 40px; top: 1105px; font-size: 38px; }
  .location { left: 350px; top: 1100px; }
  .contact { left: 560px; top: 1100px; }
  .location .script, .contact .script { font-size: 22px; display: block; }
  .location p, .contact p { font-size: 17px; font-weight: 600; line-height: 1.25; text-transform: uppercase; }
</style>
</head>
<body>
<main class="flyer">
  <svg class="backdrop" width="819" height="1200" viewBox="0 0 819 1200">
    <defs>
      <linearGradient id="field" x1="0" y1="0" x2="0" y2="1">
        <stop offset="0" stop-color="#8fa8b8"/>
        <stop offset=".45" stop-color="#c9b08a"/>
        <stop offset="1" stop-color="#a87c55"/>
      </linearGradient>
    </defs>
    <rect role="img" aria-label="Photo of a young player sliding into base under a summer sky" x="0" y="0" width="819" height="450" fill="url(#field)"/>
    <path d="M0,360 C260,330 560,285 819,250 L819,292 C560,318 260,368 0,398 Z" fill="var(--navy)"/>
    <path d="M0,392 C260,358 560,310 819,282 L819,346 C560,362 260,408 0,446 Z" fill="var(--red)"/>
    <path d="M0,434 C260,398 560,352 819,334 L819,1200 L0,1200 Z" fill="var(--white)"/>
    <path d="M0,745 C280,770 540,800 819,790 L819,822 C540,834 280,812 0,800 Z" fill="var(--navy)"/>
    <path d="M0,812 C260,850 540,910 819,928 L819,1200 L0,1200 Z" fill="var(--red)"/>
  </svg>

  <div class="abs logo-badge"><span>KESTREL</span></div>

  <div class="abs script sport-label">Softball</div>
  <svg class="abs headline" width="625" height="110" viewBox="0 0 625 110">
    <title>Summer Camp</title>
    <text x="0" y="104" font-family="Oswald, sans-serif" font-weight="600" font-size="124" textLength="619" lengthAdjust="spacingAndGlyphs"><tspan fill="var(--red)">SUMMER</tspan><tspan fill="var(--blue)">CAMP</tspan></text>
  </svg>
  <svg class="abs year" width="46" height="112" viewBox="0 0 46 112">
    <title>2017</title>
    <text transform="translate(40,110) rotate(-90)" font-family="Oswald, sans-serif" font-weight="700" font-size="50" fill="var(--red)" textLength="106" lengthAdjust="spacingAndGlyphs">2017</text>
  </svg>
  <div class="abs script audience">for boys and girls</div>
  <p class="abs hosted">Hosted by "Kestrel Baseball" affiliated with the Harbor Comets Travel<br>Baseball &amp; Softball Club and the Maple Ridge Youth League</p>
  <div class="abs partner-mark" aria-label="Maple Ridge Youth League badge"></div>

  <div class="abs ages">
    <svg width="26" height="30" viewBox="0 0 26 30" aria-hidden="true">
      <circle cx="6" cy="5" r="4" fill="var(--red-deep)"/><rect x="2" y="10" width="8" height="18" rx="2" fill="var(--red-deep)"/>
      <circle cx="20" cy="5" r="4" fill="var(--red-deep)"/><rect x="16" y="10" width="8" height="18" rx="2" fill="var(--red-deep)"/>
    </svg>
    <div class="ages-label">Players<br>Ages</div>
  </div>
  <div class="abs ages-circle">5 - 11</div>

  <section class="abs info schedule">
    <svg class="icon" style="left:0;top:2px" width="34" height="34" viewBox="0 0 34 34" aria-hidden="true">
      <circle cx="17" cy="19" r="12" fill="none" stroke="#fff" stroke-width="3"/>
      <path d="M17 12v7l5 3" stroke="#fff" stroke-width="3" fill="none"/><rect x="13" y="2" width="8" height="4" fill="#fff"/>
    </svg>
    <div class="row"><h3>FULL DAY</h3><p>9:30AM - 2:30PM</p></div>
    <div class="dash"></div>
    <div class="row"><h3>HALF DAY</h3><p>9:30AM - 11:30AM</p></div>
  </section>

  <div class="abs divider" style="left:272px"></div>
  <section class="abs info weeks">
    <div class="script">Weeks of</div>
    <p><span class="arrow">&#9658;</span>JULY 10TH - 14TH</p>
    <div class="sep"></div>
    <p><span class="arrow">&#9658;</span>JULY 17TH - 21ST.</p>
  </section>
  <div class="abs divider" style="left:555px"></div>

  <section class="abs info price">
    <div class="script">Cost:</div>
    <svg class="icon" style="left:0;top:52px" width="40" height="40" viewBox="0 0 40 40" aria-hidden="true">
      <circle cx="20" cy="20" r="19" fill="#fff"/>
      <text x="20" y="28" text-anchor="middle" font-family="Oswald, sans-serif" font-weight="700" font-size="24" fill="var(--red)">$</text>
    </svg>
    <div class="lines">$295 / FULL DAY<br>$195/ HALF DAY</div>
  </section>

  <div class="abs footer-rule"></div>
  <div class="abs info script register">Register today!</div>

  <section class="abs info location">
    <svg class="icon" style="left:-26px;top:2px" width="18" height="24" viewBox="0 0 18 24" aria-hidden="true">
      <path d="M9 0C4 0 0 4 0 9c0 7 9 15 9 15s9-8 9-15c0-5-4-9-9-9z" fill="#fff"/><circle cx="9" cy="9" r="3.5" fill="var(--red)"/>
    </svg>
    <span class="script">Camp Location:</span>
    <p>MRYL, Route 9C<br>Birch Hollow.</p>
  </section>

  <section class="abs info contact">
    <svg class="icon" style="left:-24px;top:2px" width="14" height="24" viewBox="0 0 14 24" aria-hidden="true">
      <rect x="0" y="0" width="14" height="24" rx="3" fill="#fff"/><rect x="2" y="4" width="10" height="14" fill="var(--red)"/>
    </svg>
    <span class="script">Contact:</span>
    <p>Phone 555-240-7813<br>Email info@kestrelball.example</p>
  </section>
</main>
</body>
</html>
```